Veldmark Supplies Business Card

Professional business card that stand out to our potential customers. Front and back with clean modern design

Industry/Entity Type

Oil and gas

Contact Information for Business Card

Name, address, website , office phone and cell number

Requirements
Must have
• Editable files for each employee

```html
<!DOCTYPE html>
<html lang="en">
<head>
<meta charset="utf-8">
<title>Veldmark Supplies Business Card</title>
<link href="https://fonts.googleapis.com/css2?family=Montserrat:wght@500;700;800&display=swap" rel="stylesheet">
<style>
  :root {
    --page: #2b2b2b;
    --card: #231f20;
    --red: #ed1c24;
    --green: #1a9a48;
    --blue: #16b3d6;
    --white: #f4f4f4;
  }
  * { box-sizing: border-box; margin: 0; padding: 0; }
  html, body {
    width: 1200px; height: 988px; overflow: hidden;
    background: var(--page);
    font-family: "Montserrat", sans-serif;
  }
  .canvas {
    position: relative; width: 1200px; height: 988px;
  }
  .card {
    position: absolute; left: 250px; width: 700px; height: 400px;
    background: var(--card); border-radius: 22px;
    overflow: hidden;
  }
  .card-front { top: 70px; }
  .card-back { top: 518px; }

  /* front */
  .brand {
    position: absolute; left: 0; right: 0; top: 0; bottom: 0;
    display: flex; align-items: center; justify-content: center; gap: 18px;
  }
  .brand-mark {
    width: 46px; height: 46px; background: var(--red);
  }
  .brand-name {
    font-weight: 800; font-size: 40px; letter-spacing: 2px;
    color: var(--red); text-transform: uppercase;
  }

  /* back */
  .back-brand {
    position: absolute; left: 52px; top: 46px;
    display: flex; align-items: center; gap: 12px;
  }
  .back-brand .brand-mark { width: 26px; height: 26px; }
  .back-brand .brand-name { font-size: 24px; letter-spacing: 1.5px; }

  .accent-bar {
    position: absolute; left: 0; top: 168px; width: 14px; height: 62px;
    background: var(--red); border-radius: 0 6px 6px 0;
  }
  .person { position: absolute; left: 52px; top: 160px; }
  .person-name { font-weight: 800; font-size: 38px; line-height: 1.1; }
  .person-name .first { color: var(--red); }
  .person-name .last { color: var(--green); }
  .person-role {
    font-weight: 500; font-size: 17px; color: var(--white); margin-top: 4px;
  }
  .divider {
    position: absolute; left: 52px; top: 250px; width: 22px; height: 2px;
    background: var(--red);
  }
  .contacts {
    position: absolute; left: 52px; top: 266px; list-style: none;
  }
  .contacts li {
    display: flex; align-items: center; gap: 12px;
    font-size: 17px; font-weight: 500; color: var(--white);
    height: 24px;
  }
  .contacts svg { width: 16px; height: 16px; flex: none; }
  .icon-red { fill: var(--red); stroke: var(--red); }
  .icon-green { fill: var(--green); stroke: var(--green); }
</style>
</head>
<body>
<main class="canvas">

  <section class="card card-front" aria-label="Card front">
    <div class="brand">
      <span class="brand-mark"></span>
      <span class="brand-name">Veldmark Supplies</span>
    </div>
  </section>

  <section class="card card-back" aria-label="Card back">
    <div class="back-brand">
      <span class="brand-mark"></span>
      <span class="brand-name">Veldmark Supplies</span>
    </div>

    <span class="accent-bar"></span>
    <div class="person">
      <p class="person-name"><span class="first">Daniel</span> <span class="last">Morrow</span></p>
      <p class="person-role">Manager</p>
    </div>

    <span class="divider"></span>

    <ul class="contacts">
      <li>
        <svg viewBox="0 0 16 16" class="icon-red" aria-hidden="true"><path d="M3 1.5l3 .5 1 3.5-2 1.3a9 9 0 0 0 4.2 4.2l1.3-2 3.5 1 .5 3c-.4.8-1.3 1.2-2.2 1C6.5 13.3 2.7 9.5 2 3.7c-.1-.9.3-1.8 1-2.2z" stroke="none"/></svg>
        1-555-014-0177
      </li>
      <li>
        <svg viewBox="0 0 16 16" class="icon-green" aria-hidden="true"><rect x="1" y="3" width="14" height="10" rx="1" stroke="none"/><path d="M1.5 3.5L8 9l6.5-5.5" fill="none" stroke="#231f20" stroke-width="1.4"/></svg>
        dmorrow@keltraparts.vn
      </li>
      <li>
        <svg viewBox="0 0 16 16" class="icon-red" aria-hidden="true"><g fill="none" stroke-width="1.3"><circle cx="8" cy="8" r="6.5"/><ellipse cx="8" cy="8" rx="3" ry="6.5"/><path d="M1.5 8h13M2.5 4.5h11M2.5 11.5h11"/></g></svg>
        www.keltraparts.vn
      </li>
      <li>
        <svg viewBox="0 0 16 16" class="icon-green" aria-hidden="true"><g fill="none" stroke-width="1.3"><circle cx="8" cy="8" r="6.5"/><ellipse cx="8" cy="8" rx="3" ry="6.5"/><path d="M1.5 8h13M2.5 4.5h11M2.5 11.5h11"/></g></svg>
        www.keltraparts.com
      </li>
      <li>
        <svg viewBox="0 0 16 16" class="icon-red" aria-hidden="true"><path d="M8 1a5 5 0 0 0-5 5c0 3.6 5 9 5 9s5-5.4 5-9a5 5 0 0 0-5-5z" stroke="none"/><circle cx="8" cy="6" r="1.8" fill="#231f20" stroke="none"/></svg>
        Riverside City, Vietnam
      </li>
    </ul>
  </section>

</main>
</body>
</html>
```